Cyber Security Site Design (Products & Consulting)

I need my website redesigned to be engaging, clean, efficient and modern. My company (when its up and running) is going to be concentrated on two things: a few specific products for cyber security as well as cyber security consulting services. The background I bring to the field is having worked with small companies all the way to the largest government organizations and advising them on their security posture and how to improve it. We need the ability to add products and services easily.

For a sample product, you can use either Tarnet (http://www.tarnet-relay.org/) or Verodyne Ashmantle (https://www.verodyne.com/products/relay-hx-and-fortified-edge-portal).

It will replace https://lumerafieldworks.com/

Target Market(s)

Cyber Security professionals in all verticals

Coding

Coded - Design and coding required

Number of Pages Required

4 page

Font styles to use
Sans Serif

Colors
6b449b

Requirements
Must have
• Ability to easily modify
• Have main page
• Have product specific pages
• Have consulting services pages
• Have executive team information
• Clean, modern design
• Usage of the logo and its color scheme
Nice to have
• I like the idea of a left collapsed sidebar (so icons only) that can expand for text.
• I am also open to a very unique landing page, possibly a shape in the middle (hexagons maybe?) with each of the options there.
Should not have
• Nothing that looks like it came out of a hacker movie

```html
<!DOCTYPE html>
<html lang="en">
<head>
<meta charset="utf-8">
<title>Lumera Fieldworks — Cyber Security Operations</title>
<link rel="stylesheet" href="https://fonts.googleapis.com/css2?family=Exo+2:wght@600;700;800&family=Open+Sans:wght@400;600;700&display=swap">
<style>
:root{
  --purple:#6b449b;
  --purple-deep:#55327f;
  --footer:#5d3a8a;
  --ink:#222222;
  --text:#4a4a4a;
  --grey-band:#5a5a5a;
  --light:#f2f2f2;
  --white:#ffffff;
  --dark:#1c1c1c;
}
*{box-sizing:border-box;margin:0;padding:0}
html,body{width:1200px;height:3586px;overflow:hidden}
body{position:relative;font-family:"Open Sans",Arial,sans-serif;color:var(--text);background:var(--white)}
.abs{position:absolute}
.display{font-family:"Exo 2",Arial,sans-serif;font-weight:800;text-transform:uppercase;letter-spacing:2px}
.brand{display:flex;align-items:center;gap:10px;font-family:"Exo 2",Arial,sans-serif;font-weight:700;text-transform:uppercase;letter-spacing:1px;color:var(--purple);white-space:nowrap}
.brand .dot{width:30px;height:30px;border-radius:50%;background:var(--purple);flex:none}

/* hero */
.hero{left:0;top:0;width:1200px;height:602px;background:linear-gradient(180deg,#4d4d4d 0%,#3a3a3a 45%,#2a2a2a 100%)}
.topbar-social{left:145px;top:8px;display:flex;gap:8px}
.topbar-social span{width:24px;height:24px;border-radius:50%;background:var(--white)}
.topbar-contact{top:8px;display:flex;align-items:center;gap:8px;color:var(--white);font-size:12px;font-weight:600}
.topbar-contact .ic{width:24px;height:24px;border-radius:50%;background:var(--white);display:flex;align-items:center;justify-content:center}
.logo-panel{left:140px;top:46px;width:290px;height:90px;background:var(--white);border-radius:0 40px 0 0;padding-left:20px;display:flex;align-items:center}
.logo-panel .brand{font-size:17px;letter-spacing:.5px;gap:8px}
.logo-panel .brand .dot{width:26px;height:26px}
.nav{left:430px;top:48px;width:630px;height:87px;background:var(--purple);border-radius:40px 0 0 0;display:flex;align-items:center;padding-left:40px;gap:32px}
.nav a{color:var(--white);font-size:13px;font-weight:600;text-decoration:none;text-transform:uppercase}
.hero-title{left:0;top:228px;width:1200px;text-align:center;color:var(--white);font-size:40px;line-height:54px}
.hero-sub{left:0;top:352px;width:1200px;text-align:center;color:#e4e4e4;font-size:14px}
.btn{display:flex;align-items:center;height:40px;background:var(--purple);color:var(--white);font-size:13px;font-weight:700;text-transform:uppercase;border-radius:0 20px 20px 0;padding-right:24px;gap:14px;letter-spacing:.5px}
.btn .knob{width:44px;height:40px;background:var(--white);border-radius:20px 0 0 20px;border:2px solid var(--purple);display:flex;align-items:center;justify-content:center}
.btn .knob i{width:16px;height:16px;border-radius:50%;background:var(--purple);display:block}

/* headings */
.sec-title{left:0;width:1200px;text-align:center;color:var(--purple);font-size:34px}
.rule{height:3px;width:70px;background:var(--grey-band)}

/* about */
.about-head{left:140px;top:668px;display:flex;align-items:center;gap:16px}
.about-head h2{font-size:32px;color:var(--ink)}
.about-head .brand{font-size:22px}
.about-copy{left:140px;top:756px;width:585px;font-size:13.5px;line-height:21px;color:#333;text-align:justify}
.about-copy p+p{margin-top:10px}
.about-photo{left:752px;top:682px;width:306px;height:370px;border:4px solid var(--purple);border-radius:0 46px 0 46px;background:linear-gradient(160deg,#d9d2c8,#8f8a86 55%,#4c4a50)}

/* services */
.services{left:0;top:1124px;width:1200px;height:602px;background:var(--light)}
.svc{width:220px;text-align:center}
.svc h3{font-family:"Exo 2",Arial,sans-serif;font-size:14px;font-weight:700;color:var(--ink);line-height:18px}
.svc p{font-size:12px;line-height:16px;color:#444;margin-top:8px}
.svc .pin{width:18px;height:18px;border-radius:50%;margin:8px auto 0}

/* products */
.prod-label{font-family:"Exo 2",Arial,sans-serif;font-weight:700;font-size:15px;color:var(--ink);display:flex;align-items:center;gap:6px;white-space:nowrap}
.prod-centre{left:508px;top:2092px;width:180px;justify-content:center;font-size:17px;line-height:19px;letter-spacing:.5px;gap:8px}
.prod-centre .dot{width:24px;height:24px}

/* team */
.team{left:0;top:2350px;width:1200px;height:514px;background:linear-gradient(180deg,#3a3a3a,#202020)}
.team-title{color:var(--white)}
.card{top:2496px;width:207px;height:294px;background:var(--white);border-radius:0 44px 0 0;overflow:hidden}
.card .photo{height:206px;border-radius:0 44px 0 0}
.card h4{font-size:13px;color:var(--purple);text-align:center;margin-top:10px;font-weight:700;white-space:nowrap}
.card .role{font-size:10px;color:#555;text-align:center;text-transform:uppercase;margin-top:2px}
.card .social{display:flex;justify-content:center;gap:6px;margin-top:8px}
.card .social span{width:20px;height:20px;border-radius:50%;background:var(--purple)}

/* testimonials */
.t-photo{left:140px;top:2998px;width:152px;height:132px;border-radius:0 36px 0 36px;background:linear-gradient(150deg,#8aa7b8,#4f6a7a)}
.t-quote{left:325px;top:3008px;width:745px;font-size:12.5px;line-height:20px;color:#555}
.t-name{left:330px;top:3108px;font-size:14px;font-weight:700;color:var(--purple)}
.t-dots{left:968px;top:3114px;display:flex;gap:5px}
.t-dots span{width:9px;height:9px;border-radius:50%;background:#bbb}
.t-dots span:first-child{background:var(--purple)}

/* footer */
.footer{left:0;top:3203px;width:1200px;height:347px;background:var(--footer)}
.f-head{font-size:15px;font-weight:700;color:var(--white)}
.f-links{list-style:none;font-size:12px;color:var(--white);line-height:25px;text-transform:uppercase}
.f-links li::before{content:"›";margin-right:8px}
.field{width:215px;height:28px;background:var(--white);border-radius:3px;font-size:11px;color:#666;padding:6px 8px}
.f-contact{font-size:12.5px;line-height:19px;color:var(--white);display:flex;gap:10px}
.copyright{left:0;top:3550px;width:1200px;height:36px;background:var(--dark);color:var(--white);font-size:11px;text-align:center;line-height:36px}
</style>
</head>
<body>

<!-- HERO -->
<div class="abs hero" role="img" aria-label="Dimmed photograph of a modern office desk with a computer monitor"></div>
<div class="abs topbar-social"><span></span><span></span><span></span><span></span></div>
<div class="abs topbar-contact" style="left:728px">
  <span class="ic"><svg width="12" height="12" viewBox="0 0 24 24"><path fill="#333" d="M6.6 10.8a15 15 0 0 0 6.6 6.6l2.2-2.2a1 1 0 0 1 1-.25 11.4 11.4 0 0 0 3.6.57 1 1 0 0 1 1 1V20a1 1 0 0 1-1 1A17 17 0 0 1 3 4a1 1 0 0 1 1-1h3.5a1 1 0 0 1 1 1c0 1.25.2 2.45.57 3.57a1 1 0 0 1-.25 1z"/></svg></span>+100 555 0142
</div>
<div class="abs topbar-contact" style="left:875px">
  <span class="ic"><svg width="12" height="12" viewBox="0 0 24 24"><path fill="#333" d="M2 5h20v14H2zm2 2v.5l8 5 8-5V7z"/></svg></span>info@lumerafieldworks.com
</div>
<div class="abs logo-panel"><div class="brand"><span class="dot"></span>Lumera Fieldworks</div></div>
<nav class="abs nav"><a>Home</a><a>About Us</a><a>Services</a><a>Products</a><a>Our Team</a><a>Contact Us</a></nav>
<h1 class="abs hero-title display">Creative Solutions for Cyber<br>Security Operations</h1>
<p class="abs hero-sub">We are located in the Corvale / Ashby, NT, USA area but are able to work with clients world-wide.</p>
<div class="abs btn" style="left:512px;top:396px"><span class="knob"><i></i></span>Contact Us</div>

<!-- ABOUT -->
<div class="abs about-head"><h2 class="display">About</h2><div class="brand"><span class="dot"></span>Lumera Fieldworks</div></div>
<div class="abs rule" style="left:140px;top:716px;background:var(--purple)"></div>
<div class="abs about-copy">
  <p>We are a company that takes its roots from the idea of providing appropriate and creative solutions for cyber security operations, development and management. We have a mission first mindset for our clients and their objectives.</p>
  <p>Integer luctus diam sem, sit amet eleifend nulla ultricies non. Cras feugiat nulla id cursus dictum. Curabitur a dictum magna, id fermentum tellus. Vestibulum interdum sem eu ligula iaculis, in faucibus quam placerat. Pellentesque nunc mi, rutrum vitae massa quis, tincidunt luctus sem. Praesent viverra sit amet risus sit amet tempus. Etiam ultricies tellus vel bibendum scelerisque. Sed vehicula vehicula odio a eleifend. Sed nisi dui, tincidunt quis tempor pharetra, auctor ullamcorper ligula. Vestibulum ante ipsum primis in faucibus orci luctus et ultrices posuere cubilia Curae; Orci varius natoque penatibus et magnis dis parturient montes, nascetur ridiculus mus. Proin ac consequat nisi, eget feugiat purus.</p>
</div>
<div class="abs btn" style="left:140px;top:1010px"><span class="knob"><i></i></span>Contact Us</div>
<div class="abs about-photo" role="img" aria-label="Photograph of three colleagues reviewing work on a laptop"></div>

<!-- SERVICES -->
<div class="abs services"></div>
<h2 class="abs sec-title display" style="top:1188px">Our Services</h2>
<div class="abs rule" style="left:565px;top:1238px"></div>

<div class="abs svc" style="left:160px;top:1272px"><h3>Incident Response<br>Services</h3><p>Duis autem vel eum iriure do<br>in hendrerit in vulputate.</p><div class="pin" style="background:var(--purple)"></div></div>
<div class="abs svc" style="left:427px;top:1272px"><h3>Network Security<br>Services</h3><p>Duis autem vel eum iriure do<br>in hendrerit in vulputate.</p><div class="pin" style="background:var(--purple)"></div></div>
<div class="abs svc" style="left:690px;top:1272px"><h3>Managed Security<br>Services</h3><p>Duis autem vel eum iriure do<br>in hendrerit in vulputate.</p><div class="pin" style="background:var(--purple)"></div></div>

<svg class="abs" style="left:0;top:1370px" width="1200" height="180" viewBox="0 0 1200 180" aria-hidden="true">
  <g fill="none" stroke-width="30">
    <path d="M188 90 A82 82 0 0 0 352 90" stroke="var(--purple)"/>
    <path d="M320 90 A82 82 0 0 1 484 90" stroke="var(--grey-band)"/>
    <path d="M455 90 A82 82 0 0 0 619 90" stroke="var(--purple)"/>
    <path d="M588 90 A82 82 0 0 1 752 90" stroke="var(--grey-band)"/>
    <path d="M718 90 A82 82 0 0 0 882 90" stroke="var(--purple)"/>
    <path d="M855 90 A82 82 0 0 1 1019 90" stroke="var(--grey-band)"/>
  </g>
  <g fill="#fff">
    <circle cx="270" cy="90" r="50"/><circle cx="402" cy="90" r="50"/><circle cx="537" cy="90" r="50"/>
    <circle cx="670" cy="90" r="50"/><circle cx="800" cy="90" r="50"/><circle cx="937" cy="90" r="50"/>
  </g>
  <g fill="var(--ink)" stroke="var(--ink)" stroke-width="3">
    <path d="M260 86 v-10 a10 10 0 0 1 20 0 v10" fill="none"/><rect x="254" y="86" width="32" height="24" stroke="none"/>
    <rect x="389" y="68" width="24" height="32" fill="none"/><path d="M394 78h14M394 85h10" /><path d="M408 92 l10 -4 10 4 v6 q0 8 -10 12 q-10 -4 -10 -12z" stroke="none"/>
    <rect x="515" y="70" width="44" height="30" fill="none"/><path d="M507 106h60" /><path d="M537 76 l9 16 h-18z" stroke="none"/>
    <path d="M650 90 a12 12 0 0 1 6 -22 a16 16 0 0 1 30 4 a10 10 0 0 1 2 18z" stroke="none"/><rect x="662" y="92" width="18" height="14" stroke="none"/><path d="M665 92 v-5 a6 6 0 0 1 12 0 v5" fill="none"/>
    <rect x="778" y="70" width="44" height="32" fill="none"/><path d="M800 102 v6 M788 110 h24"/><rect x="792" y="84" width="16" height="12" stroke="none"/><path d="M795 84 v-4 a5 5 0 0 1 10 0 v4" fill="none"/>
    <rect x="915" y="74" width="38" height="26" fill="none"/><path d="M915 74 l19 14 19 -14" fill="none"/><rect x="942" y="92" width="14" height="12" stroke="none"/>
  </g>
</svg>

<div class="abs svc" style="left:292px;top:1552px"><h3>Cyber Security<br>Services</h3><p>Duis autem vel eum iriure do<br>in hendrerit in vulputate.</p><div class="pin" style="background:var(--ink)"></div></div>
<div class="abs svc" style="left:560px;top:1552px"><h3>Cloud Security<br>Services</h3><p>Duis autem vel eum iriure do<br>in hendrerit in vulputate.</p><div class="pin" style="background:var(--ink)"></div></div>
<div class="abs svc" style="left:827px;top:1552px"><h3>Email Security<br>Services</h3><p>Duis autem vel eum iriure do<br>in hendrerit in vulputate.</p><div class="pin" style="background:var(--ink)"></div></div>

<!-- PRODUCTS -->
<h2 class="abs sec-title display" style="top:1788px">Our Products</h2>
<div class="abs rule" style="left:565px;top:1838px"></div>

<svg class="abs" style="left:0;top:1860px" width="1200" height="420" viewBox="0 1860 1200 420" aria-hidden="true">
  <path d="M502 2230 A150 150 0 1 1 694 2230" fill="none" stroke="var(--ink)" stroke-width="7"/>
  <g stroke="var(--purple)" stroke-width="2" fill="var(--purple)">
    <line x1="598" y1="1900" x2="598" y2="1918"/><circle cx="598" cy="1900" r="4"/>
    <line x1="748" y1="2009" x2="818" y2="2009" stroke="var(--ink)"/><circle cx="818" cy="2009" r="4"/>
    <line x1="792" y1="2115" x2="836" y2="2115" stroke="var(--ink)"/><circle cx="836" cy="2115" r="4"/>
    <line x1="738" y1="2230" x2="836" y2="2230" stroke="var(--ink)"/><circle cx="836" cy="2230" r="4"/>
    <line x1="448" y1="2009" x2="378" y2="2009" stroke="var(--ink)"/><circle cx="378" cy="2009" r="4"/>
    <line x1="404" y1="2115" x2="360" y2="2115" stroke="var(--ink)"/><circle cx="360" cy="2115" r="4"/>
    <line x1="458" y1="2230" x2="360" y2="2230" stroke="var(--ink)"/><circle cx="360" cy="2230" r="4"/>
  </g>
  <g fill="#fff" stroke-width="6">
    <circle cx="598" cy="1965" r="42" stroke="var(--purple)"/>
    <circle cx="704" cy="2009" r="42" stroke="var(--purple)"/>
    <circle cx="748" cy="2115" r="42" stroke="var(--purple)"/>
    <circle cx="694" cy="2230" r="42" stroke="var(--grey-band)"/>
    <circle cx="492" cy="2009" r="42" stroke="var(--purple)"/>
    <circle cx="448" cy="2115" r="42" stroke="var(--purple)"/>
    <circle cx="502" cy="2230" r="42" stroke="var(--grey-band)"/>
  </g>
  <g fill="var(--purple)" stroke="var(--purple)" stroke-width="2.5">
    <path d="M598 1947 l16 6 v10 q0 14 -16 20 q-16 -6 -16 -20 v-10z" stroke="none"/>
    <rect x="690" y="1996" width="28" height="20" fill="none"/><circle cx="704" cy="2006" r="5" stroke="none"/>
    <rect x="736" y="2097" width="24" height="32" fill="none"/><path d="M741 2106h14M741 2113h14M741 2120h9"/>
    <rect x="676" y="2216" width="36" height="24" fill="none"/><path d="M694 2221 l8 14 h-16z" stroke="none"/>
    <rect x="474" y="1995" width="36" height="24" fill="none"/><path d="M486 2024 h12"/><path d="M492 2000 l8 4 v5 q0 6 -8 9 q-8 -3 -8 -9 v-5z" stroke="none"/>
    <path d="M432 2115 a9 9 0 0 1 4 -17 a12 12 0 0 1 24 3 a8 8 0 0 1 2 14z" stroke="none"/><rect x="441" y="2117" width="14" height="12" stroke="none"/>
    <rect x="484" y="2219" width="36" height="24" fill="none"/><path d="M484 2219 l18 12 18 -12" fill="none"/>
  </g>
</svg>
<div class="abs brand prod-centre"><span class="dot"></span><span>Lumera<br>Fieldworks</span></div>

<div class="abs prod-label" style="left:0;width:1196px;justify-content:center;top:1872px">Integrated Cyber Defense</div>
<div class="abs prod-label" style="left:826px;top:1999px">Advance Threat Protection</div>
<div class="abs prod-label" style="left:844px;top:2105px">Information Protection</div>
<div class="abs prod-label" style="left:844px;top:2220px">Endpoint Security</div>
<div class="abs prod-label" style="right:830px;top:1999px">Small Business Products</div>
<div class="abs prod-label" style="right:848px;top:2105px">Network Security</div>
<div class="abs prod-label" style="right:848px;top:2220px">Email Security</div>

<!-- TEAM -->
<div class="abs team" role="img" aria-label="Dark photograph of a laptop keyboard on a desk"></div>
<h2 class="abs sec-title display team-title" style="top:2412px">Our Team</h2>
<div class="abs rule" style="left:565px;top:2462px;background:#ddd"></div>

<div class="abs card" style="left:140px"><div class="photo" role="img" aria-label="Portrait of the founder and CEO" style="background:linear-gradient(160deg,#b9b3ad,#6f6a68)"></div><h4>Marten Olsgaard Revik</h4><div class="role">Founder &amp; CEO</div><div class="social"><span></span><span></span><span></span><span></span></div></div>
<div class="abs card" style="left:378px"><div class="photo" role="img" aria-label="Portrait of the co-founder" style="background:linear-gradient(160deg,#cfd8de,#8e9aa3)"></div><h4>Tobin Harlow</h4><div class="role">Co-Founder</div><div class="social"><span></span><span></span><span></span><span></span></div></div>
<div class="abs card" style="left:616px"><div class="photo" role="img" aria-label="Portrait of the CTO" style="background:linear-gradient(160deg,#d7c9b6,#8c7a68)"></div><h4>Celia Brandt</h4><div class="role">CTO</div><div class="social"><span></span><span></span><span></span><span></span></div></div>
<div class="abs card" style="left:854px"><div class="photo" role="img" aria-label="Portrait of the manager" style="background:linear-gradient(160deg,#e3e3e3,#9aa0b0)"></div><h4>Idris Nwankel</h4><div class="role">Manager</div><div class="social"><span></span><span></span><span></span><span></span></div></div>

<!-- TESTIMONIALS -->
<h2 class="abs sec-title display" style="top:2928px">Testimonials</h2>
<div class="abs rule" style="left:565px;top:2978px"></div>
<div class="abs t-photo" role="img" aria-label="Portrait of a client giving a testimonial"></div>
<svg class="abs" style="left:325px;top:3002px" width="22" height="16" viewBox="0 0 22 16" aria-hidden="true"><path fill="#cfcfcf" d="M0 16V9Q0 2 8 0v3Q4 4 4 8h4v8zm12 0V9q0-7 8-9v3q-4 1-4 5h4v8z"/></svg>
<p class="abs t-quote" style="text-indent:30px">Lorem ipsum dolor sit amet, consectetuer adipiscing elit, sed diam nonummy nibh euismod tincidunt ut laoreet dolore magna aliquam erat volutpat. Ut wisi enim ad minim veniam, quis nostrud exerci tation ullamcorper suscipit lobortis nisl ut aliquip ex ea commodo consequat. Duis autem vel eum iriure dolor in hendrerit in vulputate velit esse molestie consequat, vel illum dolore eu feugiat nulla facilisis.</p>
<div class="abs t-name">- Mr. Elan Vostrick</div>
<div class="abs t-dots"><span></span><span></span><span></span></div>

<!-- FOOTER -->
<footer class="abs footer"></footer>
<div class="abs f-head" style="left:140px;top:3270px">Quick Links</div>
<ul class="abs f-links" style="left:145px;top:3298px"><li>Home</li><li>About Us</li><li>Services</li><li>Products</li><li>Our Team</li><li>Contact Us</li></ul>

<div class="abs f-head" style="left:300px;top:3270px">Quick Inquiry</div>
<div class="abs field" style="left:300px;top:3304px">Name</div>
<div class="abs field" style="left:300px;top:3342px">Email</div>
<div class="abs field" style="left:300px;top:3380px;height:60px">Message</div>
<div class="abs btn" style="left:300px;top:3452px;height:32px;font-size:11px;padding-right:16px;gap:10px"><span class="knob" style="width:36px;height:32px;border-radius:16px 0 0 16px"><i style="width:12px;height:12px"></i></span>Send Message</div>

<div class="abs f-head" style="left:578px;top:3270px">Contact Details</div>
<div class="abs f-contact" style="left:578px;top:3300px;width:240px">
  <svg width="12" height="16" viewBox="0 0 12 16" style="flex:none;margin-top:2px" aria-hidden="true"><path fill="#fff" d="M6 0a6 6 0 0 1 6 6c0 4.5-6 10-6 10S0 10.5 0 6a6 6 0 0 1 6-6zm0 3.5a2.5 2.5 0 1 0 0 5 2.5 2.5 0 0 0 0-5z"/></svg>
  <span>123 euismod cidun ut laoreetmok laoreet dol magnak aliquam PG Feugait.</span>
</div>
<div class="abs f-contact" style="left:578px;top:3378px">
  <svg width="13" height="13" viewBox="0 0 24 24" style="margin-top:3px" aria-hidden="true"><path fill="#fff" d="M6.6 10.8a15 15 0 0 0 6.6 6.6l2.2-2.2a1 1 0 0 1 1-.25 11.4 11.4 0 0 0 3.6.57 1 1 0 0 1 1 1V20a1 1 0 0 1-1 1A17 17 0 0 1 3 4a1 1 0 0 1 1-1h3.5a1 1 0 0 1 1 1c0 1.25.2 2.45.57 3.57a1 1 0 0 1-.25 1z"/></svg>+100 555 0142
</div>
<div class="abs f-contact" style="left:578px;top:3410px">
  <svg width="13" height="13" viewBox="0 0 24 24" style="margin-top:3px" aria-hidden="true"><path fill="#fff" d="M2 5h20v14H2zm2 2v.5l8 5 8-5V7z"/></svg>info@lumerafieldworks.com
</div>

<div class="abs brand" style="left:874px;top:3300px;font-size:20px;color:var(--white)"><span class="dot" style="background:var(--white);width:26px;height:26px"></span>Lumera Fieldworks</div>
<div class="abs" style="left:874px;top:3380px;display:flex;gap:8px">
  <span style="width:24px;height:24px;border-radius:50%;background:var(--white)"></span>
  <span style="width:24px;height:24px;border-radius:50%;background:var(--white)"></span>
  <span style="width:24px;height:24px;border-radius:50%;background:var(--white)"></span>
</div>

<div class="abs copyright">Copyright © 2018 Lumera Cybersecurity . All Right Reserved.</div>

</body>
</html>
```